Business card for my new company (Accounting firm)

I need a business card for my new business Brightwell Advisory and Ledger SA. Our services are accounting, tax, audit and financial management. Our customers are small companies, start-ups and new companies. The final design has to show financial security, trust and growth. Please find our logo attached to the business card. Text for the business card: Brightwell Advisory and Ledger SA Tomas Varenholt Director and Founder Certified Accountant Tel. 022 418 57 34 tv@clairevalconseil.ch www.clairevalconseil.ch Rue des Vergières 27 1201 Geneva
Target Market(s)
Our customers are small companies, start-ups and new companies.
Industry/Entity Type
Finance And Accounting
Contact Information for Business Card
Claireval Conseil et Comptes SA
Tomas Varenholt
Directeur et Fondateur
Expert-comptable diplômé
Tél. 022 418 57 34
tv@clairevalconseil.ch
www.clairevalconseil.ch
Rue des Vergières 27
1201 Genève

```html
<!DOCTYPE html>
<html lang="fr">
<head>
<meta charset="utf-8">
<title>Claireval Conseil et Comptes SA – Carte de visite</title>
<link rel="stylesheet" href="https://fonts.googleapis.com/css2?family=Roboto:wght@400;500;700&display=swap">
<style>
  :root {
    --bg: #e4e5e7;
    --blue-light: #2f9fd4;
    --blue-mid: #1f7fb8;
    --blue-deep: #175b8c;
    --blue-name: #1a5e96;
    --ink: #333638;
    --ink-soft: #5a5d60;
    --paper: #f4f4f4;
    --white: #ffffff;
  }
  * { box-sizing: border-box; margin: 0; padding: 0; }
  html, body { width: 1200px; height: 726px; overflow: hidden; }
  body {
    background: var(--bg);
    font-family: "Roboto", Arial, sans-serif;
    display: flex;
    align-items: center;
    justify-content: center;
    gap: 60px;
  }
  .card {
    width: 520px;
    height: 300px;
    border-radius: 4px;
    position: relative;
    overflow: hidden;
    box-shadow: 0 6px 18px rgba(0,0,0,0.12);
  }

  /* Front */
  .card-front {
    background: linear-gradient(160deg, var(--blue-light) 0%, var(--blue-mid) 55%, var(--blue-deep) 100%);
    color: var(--white);
    display: flex;
    flex-direction: column;
    align-items: center;
    justify-content: center;
    text-align: center;
  }
  .brand {
    display: flex;
    align-items: center;
    gap: 12px;
  }
  .brand-mark {
    width: 18px;
    height: 18px;
    background: var(--white);
  }
  .brand-name {
    font-weight: 500;
    font-size: 46px;
    letter-spacing: 5px;
    line-height: 1;
  }
  .brand-tagline {
    font-weight: 400;
    font-size: 15px;
    letter-spacing: 5px;
    margin-top: 8px;
  }
  .front-url {
    font-weight: 500;
    font-size: 15px;
    margin-top: 30px;
    letter-spacing: 0.3px;
  }

  /* Back */
  .card-back {
    background: var(--paper);
    color: var(--ink);
  }
  .back-block {
    position: absolute;
    top: 0; right: 0;
    width: 150px;
    height: 100%;
    background: linear-gradient(180deg, var(--blue-light), var(--blue-deep));
  }
  .back-content {
    position: absolute;
    left: 34px;
    top: 34px;
    width: 320px;
  }
  .card-back .brand-name { color: var(--ink); font-size: 40px; }
  .card-back .brand-tagline { color: var(--ink-soft); font-size: 13px; margin-top: 6px; }
  .person {
    margin-top: 26px;
  }
  .person-name {
    color: var(--blue-name);
    font-weight: 700;
    font-size: 19px;
  }
  .person-role {
    font-size: 12px;
    color: var(--ink-soft);
    line-height: 1.35;
    margin-top: 3px;
  }
  .contacts {
    list-style: none;
    margin-top: 12px;
    font-size: 13.5px;
    color: var(--ink);
  }
  .contacts li {
    display: flex;
    align-items: center;
    gap: 10px;
    line-height: 1.55;
  }
  .contacts svg { width: 12px; height: 12px; fill: var(--ink); flex: none; }
  .address { margin-top: 4px; font-size: 13.5px; }
</style>
</head>
<body>

  <section class="card card-front" aria-label="Recto">
    <div class="brand">
      <span class="brand-mark"></span>
      <span class="brand-name">CLAIREVAL</span>
    </div>
    <div class="brand-tagline">CONSEIL ET COMPTES</div>
    <div class="front-url">www.clairevalconseil.ch</div>
  </section>

  <section class="card card-back" aria-label="Verso">
    <div class="back-block"></div>
    <div class="back-content">
      <div class="brand-name">CLAIREVAL</div>
      <div class="brand-tagline">CONSEIL ET COMPTES</div>

      <div class="person">
        <div class="person-name">Tomas Varenholt</div>
        <div class="person-role">Directeur et Fondateur<br>Expert-comptable diplômé</div>
      </div>

      <ul class="contacts">
        <li>
          <svg viewBox="0 0 24 24" aria-hidden="true"><path d="M6.6 10.8a15 15 0 0 0 6.6 6.6l2.2-2.2a1 1 0 0 1 1-.25 11.4 11.4 0 0 0 3.6.57 1 1 0 0 1 1 1V20a1 1 0 0 1-1 1A17 17 0 0 1 3 4a1 1 0 0 1 1-1h3.5a1 1 0 0 1 1 1c0 1.25.2 2.45.57 3.6a1 1 0 0 1-.25 1z"/></svg>
          022 418 57 34
        </li>
        <li>
          <svg viewBox="0 0 24 24" aria-hidden="true"><path d="M2 5h20v14H2zm2 2v.4l8 5 8-5V7zm0 2.8V17h16V9.8l-8 5z"/></svg>
          tv@clairevalconseil.ch
        </li>
        <li>
          <svg viewBox="0 0 24 24" aria-hidden="true"><path d="M12 2a10 10 0 1 0 0 20 10 10 0 0 0 0-20zm6.9 6h-3a15 15 0 0 0-1.3-3.6A8 8 0 0 1 18.9 8zM12 4a13 13 0 0 1 1.9 4h-3.8A13 13 0 0 1 12 4zM4.3 14a8 8 0 0 1 0-4h3.4a16 16 0 0 0 0 4zm.8 2h3a15 15 0 0 0 1.3 3.6A8 8 0 0 1 5.1 16zm3-8h-3a8 8 0 0 1 4.3-3.6A15 15 0 0 0 8.1 8zM12 20a13 13 0 0 1-1.9-4h3.8A13 13 0 0 1 12 20zm2.3-6H9.7a14 14 0 0 1 0-4h4.6a14 14 0 0 1 0 4zm.3 5.6a15 15 0 0 0 1.3-3.6h3a8 8 0 0 1-4.3 3.6zm1.7-5.6a16 16 0 0 0 0-4h3.4a8 8 0 0 1 0 4z"/></svg>
          www.clairevalconseil.ch
        </li>
      </ul>
      <div class="address">Rue des Vergières 27 1201 Genève</div>
    </div>
  </section>

</body>
</html>
```